business card deign

Logo needs the following on it.
1. attached logo
2. Tagline - "From chilled drinks to good times...we bring it all!"
3. Name- Dalton Pikes, Founder and CPO
4. Address - 412 E. Carver Avenue, Ste 2207, Tampa, FL. 33917
5. Phone - 555.318.4726

```html
<!DOCTYPE html>
<html lang="en">
<head>
<meta charset="utf-8">
<title>Brimley Business Card</title>
<link rel="stylesheet" href="https://fonts.googleapis.com/css2?family=Montserrat:wght@300;400;700;800&display=swap">
<style>
  :root {
    --backdrop: #141414;
    --card: #262626;
    --ink: #ffffff;
    --ink-soft: #e6e6e6;
    --pattern-light: #5a5a5a;
    --pattern-dark: #2c2c2c;
    --mascot-light: #f2f2f2;
    --mascot-shade: #bdbdbd;
  }
  * { box-sizing: border-box; margin: 0; padding: 0; }
  html, body { width: 1200px; height: 900px; overflow: hidden; }
  body {
    background: var(--backdrop);
    font-family: "Montserrat", sans-serif;
    color: var(--ink);
    display: flex;
    flex-direction: column;
    align-items: center;
    justify-content: center;
    gap: 40px;
  }
  .card {
    position: relative;
    width: 700px;
    height: 400px;
    border-radius: 22px;
    background: var(--card);
    overflow: hidden;
    box-shadow: 0 14px 30px rgba(0,0,0,.55);
  }

  /* Front */
  .brand-wordmark {
    position: absolute;
    left: 58px;
    top: 42px;
    font-weight: 800;
    font-size: 44px;
    letter-spacing: 24px;
  }
  .identity {
    position: absolute;
    left: 40px;
    top: 128px;
  }
  .identity .marker {
    position: absolute;
    left: 0;
    top: 2px;
    width: 16px;
    height: 38px;
    background: var(--ink);
  }
  .identity .name {
    margin-left: 34px;
    font-weight: 700;
    font-size: 26px;
    line-height: 1.1;
    text-transform: uppercase;
  }
  .identity .role {
    margin-left: 34px;
    font-weight: 300;
    font-size: 17px;
  }
  .contact {
    position: absolute;
    left: 74px;
    top: 200px;
    font-weight: 300;
    font-size: 17px;
    line-height: 1.45;
    color: var(--ink-soft);
  }
  .contact .address { margin-bottom: 8px; }
  .contact .line { display: flex; align-items: center; gap: 10px; }
  .contact svg { width: 16px; height: 16px; fill: var(--ink); }
  .mascot-area {
    position: absolute;
    right: 36px;
    bottom: 28px;
    width: 290px;
    height: 150px;
    border-radius: 16px;
    background: linear-gradient(135deg, var(--mascot-light), var(--mascot-shade));
    opacity: .9;
  }

  /* Back */
  .card-back .pattern {
    position: absolute;
    inset: 0;
    background: linear-gradient(120deg, var(--pattern-dark) 0%, var(--pattern-light) 55%, var(--pattern-dark) 100%);
    opacity: .55;
  }
  .back-content {
    position: absolute;
    inset: 0;
    display: flex;
    flex-direction: column;
    align-items: center;
    justify-content: center;
    gap: 26px;
  }
  .logo-lockup {
    display: flex;
    align-items: center;
    gap: 16px;
  }
  .logo-lockup .square {
    width: 26px;
    height: 26px;
    background: var(--ink);
  }
  .logo-lockup .word {
    font-weight: 800;
    font-size: 36px;
    letter-spacing: 18px;
  }
  .tagline {
    font-weight: 400;
    font-size: 19px;
  }
</style>
</head>
<body>
  <section class="card card-front">
    <div class="brand-wordmark">BRIMLEY</div>
    <div class="identity">
      <span class="marker"></span>
      <p class="name">Dalton Pikes</p>
      <p class="role">Founder and CPO</p>
    </div>
    <div class="contact">
      <p class="address">412 E. Carver Avenue<br>Ste 2207, Tampa, FL. 33917</p>
      <p class="line">
        <svg viewBox="0 0 24 24" aria-hidden="true"><path d="M6.6 10.8a15 15 0 0 0 6.6 6.6l2.2-2.2a1 1 0 0 1 1-.25 11.4 11.4 0 0 0 3.6.57 1 1 0 0 1 1 1V20a1 1 0 0 1-1 1A17 17 0 0 1 3 4a1 1 0 0 1 1-1h3.5a1 1 0 0 1 1 1c0 1.25.2 2.45.57 3.6a1 1 0 0 1-.25 1z"/></svg>
        555.318.4726
      </p>
      <p class="line">
        <svg viewBox="0 0 24 24" aria-hidden="true"><path d="M3 5h18a1 1 0 0 1 1 1v12a1 1 0 0 1-1 1H3a1 1 0 0 1-1-1V6a1 1 0 0 1 1-1zm9 7.5L20 7H4z"/></svg>
        daltonpikes@mailhub.com
      </p>
    </div>
    <div class="mascot-area" role="img" aria-label="Large white silhouette of a leaping brand mascot animal"></div>
  </section>

  <section class="card card-back">
    <div class="pattern" role="img" aria-label="Repeating pattern of faint leaping mascot silhouettes"></div>
    <div class="back-content">
      <div class="logo-lockup">
        <span class="square"></span>
        <span class="word">BRIMLEY</span>
      </div>
      <p class="tagline">From chilled drinks to good times...we bring it all!</p>
    </div>
  </section>
</body>
</html>
```